Colin Vardek Business card

Hey there, I’m hoping to have a business card designed. I’m in Real estate and just switched to a new Brokerage called: The Harbourline Property Group

The back could just be the company name maybe or whatever looks good!

I’ve attached some logos of our company and some cards my buddy had done up.

On the card:
Colin Vardek
colinvardek@mailora.com
587-412-9065
colinvardek.ca

Target Market(s)

Home buyers and sellers

Industry/Entity Type

Real Estate

Contact Information for Business Card

just looking for a cool and modern design with my picture on it. I like the idea of Black and red being used.

Requirements
Must have
• all the details provided. I'm open to anything. Just want a professional looking card.

```html
<!DOCTYPE html>
<html lang="en">
<head>
<meta charset="utf-8">
<title>Colin Vardek – Business Card</title>
<link href="https://fonts.googleapis.com/css2?family=Montserrat:wght@700;800&family=Roboto:wght@400&display=swap" rel="stylesheet">
<style>
  :root {
    --page-bg: #2a2a2c;
    --card-dark: #222125;
    --card-light: #ffffff;
    --brand-red: #d01933;
    --ink: #1f1f23;
    --muted: #555559;
    --photo-top: #e9e7e6;
    --photo-bottom: #2c3038;
  }
  * { box-sizing: border-box; margin: 0; padding: 0; }
  html, body {
    width: 1200px; height: 852px; overflow: hidden;
    background: var(--page-bg);
  }
  .canvas { position: relative; width: 1200px; height: 852px; }

  .card {
    position: absolute;
    width: 540px; height: 310px;
    border-radius: 22px;
    border: 3px solid var(--brand-red);
    overflow: hidden;
  }

  /* Back */
  .card--back { left: 70px; top: 90px; background: var(--card-dark); }
  .card--back .brand-name {
    position: absolute; left: 52px; top: 118px;
    color: #ffffff;
  }
  .brand-name {
    font-family: "Montserrat", sans-serif;
    font-weight: 800;
    font-size: 30px;
    line-height: 1.08;
    letter-spacing: 0.5px;
    text-transform: uppercase;
  }

  /* Front */
  .card--front { left: 590px; top: 452px; background: var(--card-light); }
  .card--front .brand-name {
    position: absolute; left: 34px; top: 58px;
    font-size: 21px;
    color: var(--ink);
  }
  .portrait {
    position: absolute; right: 0; top: 0;
    width: 230px; height: 310px;
    background: linear-gradient(180deg, var(--photo-top) 0%, var(--photo-top) 35%, var(--photo-bottom) 100%);
  }
  .accent-bar {
    position: absolute; left: 0; top: 200px;
    width: 10px; height: 26px;
    background: var(--brand-red);
  }
  .agent-name {
    position: absolute; left: 34px; top: 196px;
    font-family: "Montserrat", sans-serif;
    font-weight: 700; font-size: 19px;
    color: var(--brand-red);
  }
  .contact-list {
    position: absolute; left: 36px; top: 232px;
    list-style: none;
    font-family: "Roboto", sans-serif;
    font-size: 12.5px; color: var(--muted);
  }
  .contact-list li { display: flex; align-items: center; gap: 7px; height: 19px; }
  .contact-list svg { width: 12px; height: 12px; fill: var(--brand-red); flex: none; }
</style>
</head>
<body>
<main class="canvas">

  <section class="card card--back" aria-label="Card back">
    <p class="brand-name">The Harbourline<br>Property Group</p>
  </section>

  <section class="card card--front" aria-label="Card front">
    <p class="brand-name">The Harbourline<br>Property Group</p>
    <div class="portrait" role="img" aria-label="Portrait photo of Colin Vardek in a dark blazer and white shirt"></div>
    <span class="accent-bar"></span>
    <h1 class="agent-name">Colin Vardek</h1>
    <ul class="contact-list">
      <li>
        <svg viewBox="0 0 24 24" aria-hidden="true"><path d="M6.6 10.8a15.1 15.1 0 0 0 6.6 6.6l2.2-2.2c.3-.3.7-.4 1-.2 1.1.4 2.3.6 3.6.6.6 0 1 .4 1 1V20c0 .6-.4 1-1 1A17 17 0 0 1 3 4c0-.6.4-1 1-1h3.5c.6 0 1 .4 1 1 0 1.3.2 2.5.6 3.6.1.3 0 .7-.2 1z"/></svg>
        587-412-9065
      </li>
      <li>
        <svg viewBox="0 0 24 24" aria-hidden="true"><path d="M3 5h18v14H3zm2 2v.5l7 4.5 7-4.5V7zm0 2.9V17h14V9.9l-7 4.5z"/></svg>
        colinvardek@mailora.com
      </li>
      <li>
        <svg viewBox="0 0 24 24" aria-hidden="true"><path d="M12 2a10 10 0 1 0 0 20 10 10 0 0 0 0-20zm6.9 6h-2.9a15 15 0 0 0-1.4-3.6A8 8 0 0 1 18.9 8zM12 4c.8 1.2 1.5 2.5 1.9 4h-3.8c.4-1.5 1.1-2.8 1.9-4zM4.3 14a8 8 0 0 1 0-4h3.4a16 16 0 0 0 0 4zm.8 2h2.9c.3 1.3.8 2.5 1.4 3.6A8 8 0 0 1 5.1 16zM8 8H5.1a8 8 0 0 1 4.3-3.6C8.8 5.5 8.3 6.7 8 8zm4 12c-.8-1.2-1.5-2.5-1.9-4h3.8c-.4 1.5-1.1 2.8-1.9 4zm2.3-6H9.7a14 14 0 0 1 0-4h4.6a14 14 0 0 1 0 4zm.3 5.6c.6-1.1 1.1-2.3 1.4-3.6h2.9a8 8 0 0 1-4.3 3.6zm1.7-5.6a16 16 0 0 0 0-4h3.4a8 8 0 0 1 0 4z"/></svg>
        colinvardek.ca
      </li>
    </ul>
  </section>

</main>
</body>
</html>
```